Verodex business card

Business card for sustainable investment company called "Verodex". Verodex is an exchange platform selling carbon credits between buyers and sellers. Carbon Credits are an environmental commodity for reducing global carbon emissions.

the card should obviously have our logo and the theme should be sustainability/environment mixed with a trading platform.

Contact Information for Business Card

Logo, Name, Title, Phone, Email

Colors
0054AA
0677BA
7BADD7
CADEEF
E8F1F8
0094D4
00A9DD
6FCCEA
C7EBF8
E9F6FB
00AB8E
00BBA5
67D7C9
C6EFE9
E9F9F6
59FF00
82FF00
B8FF75
E3FFCB
F4FFEA

```html
<!DOCTYPE html>
<html lang="en">
<head>
<meta charset="utf-8">
<title>Verodex Business Card</title>
<link rel="stylesheet" href="https://fonts.googleapis.com/css2?family=Archivo:wght@700&family=Oswald:wght@600&display=swap">
<style>
  :root {
    --page: #ffffff;
    --card: #67d7c9;
    --ink: #0b2540;
    --accent: #0054aa;
  }
  * { margin: 0; padding: 0; box-sizing: border-box; }
  html, body {
    width: 1200px;
    height: 1200px;
    overflow: hidden;
    background: var(--page);
  }
  .canvas {
    position: relative;
    width: 1200px;
    height: 1200px;
  }
  .card {
    position: absolute;
    left: 241px;
    width: 724px;
    height: 434px;
    background: var(--card);
    color: var(--ink);
    font-family: "Archivo", Arial, sans-serif;
    font-weight: 700;
  }
  .card--front { top: 144px; }
  .card--back { top: 643px; }

  .front-brand {
    position: absolute;
    right: 56px;
    top: 62px;
    display: flex;
    align-items: center;
    gap: 10px;
    font-size: 20px;
    letter-spacing: 2px;
    line-height: 1;
  }
  .front-brand__square {
    width: 22px;
    height: 22px;
    background: var(--accent);
  }

  .identity {
    position: absolute;
    right: 357px;
    top: 192px;
    text-align: right;
  }
  .identity__name {
    font-family: "Oswald", "Arial Narrow", sans-serif;
    font-weight: 600;
    font-size: 42px;
    letter-spacing: 1.5px;
    line-height: 1;
    white-space: nowrap;
  }
  .identity__title {
    margin-top: 6px;
    font-size: 20px;
    letter-spacing: 1.5px;
    line-height: 1;
  }

  .divider {
    position: absolute;
    left: 398px;
    top: 186px;
    width: 2px;
    height: 81px;
    background: var(--ink);
  }

  .contact {
    position: absolute;
    left: 428px;
    top: 190px;
    list-style: none;
    line-height: 1;
  }
  .contact__phone {
    font-size: 22px;
    letter-spacing: 1.5px;
  }
  .contact__line {
    margin-top: 9px;
    font-size: 17px;
    letter-spacing: 1.3px;
  }

  .back-brand {
    position: absolute;
    left: 96px;
    top: 169px;
    height: 96px;
    display: flex;
    align-items: center;
    gap: 30px;
  }
  .back-brand__square {
    width: 96px;
    height: 96px;
    background: var(--accent);
  }
  .back-brand__name {
    font-size: 68px;
    letter-spacing: 4px;
    line-height: 1;
  }
</style>
</head>
<body>
<main class="canvas">
  <section class="card card--front" aria-label="Business card front">
    <div class="front-brand">
      <span class="front-brand__square"></span>
      <span>VERODEX</span>
    </div>

    <div class="identity">
      <h1 class="identity__name">TOMAS RENNICK</h1>
      <p class="identity__title">Founder</p>
    </div>

    <div class="divider"></div>

    <ul class="contact">
      <li class="contact__phone">5550142876</li>
      <li class="contact__line">tomas@verodex.com</li>
      <li class="contact__line">verodex.com</li>
    </ul>
  </section>

  <section class="card card--back" aria-label="Business card back">
    <div class="back-brand">
      <span class="back-brand__square"></span>
      <span class="back-brand__name">VERODEX</span>
    </div>
  </section>
</main>
</body>
</html>
```